Modern Business Card

Modern professional business card with more than just logo and demographic info. Something memorable.

We are a trendy/modern chiropractic group with an emphasis on neurology, hence the minimalist-type brain logo. We want to convey that modern and technical aspect with professionalism and the elite nature of our practice environment.

```html
<!DOCTYPE html>
<html lang="en">
<head>
<meta charset="utf-8">
<title>Northline Chiropractic — Business Card</title>
<link rel="stylesheet" href="https://fonts.googleapis.com/css2?family=Cinzel:wght@500&family=Montserrat:wght@400;500&display=swap">
<style>
  :root {
    --backdrop: #1b1b1c;
    --card: #2a2a2b;
    --card-edge: #232324;
    --accent: #4a86d4;
    --ink: #f2f2f2;
    --muted: #d8d8d8;
  }
  * { box-sizing: border-box; margin: 0; padding: 0; }
  html, body { width: 1200px; height: 900px; overflow: hidden; }
  body {
    background: var(--backdrop);
    font-family: "Montserrat", Arial, sans-serif;
    color: var(--ink);
    position: relative;
  }
  .card {
    position: absolute;
    left: 285px;
    width: 630px;
    height: 360px;
    background: radial-gradient(ellipse at 70% 40%, #333334 0%, var(--card) 55%, var(--card-edge) 100%);
    border-bottom: 6px solid var(--accent);
    box-shadow: 0 18px 40px rgba(0,0,0,.55);
  }
  .card--front { top: 60px; display: flex; align-items: center; justify-content: center; gap: 16px; }
  .card--back { top: 470px; display: flex; align-items: center; }

  .brand-mark { width: 14px; height: 14px; background: var(--accent); }
  .brand-name {
    font-family: "Cinzel", Georgia, serif;
    font-weight: 500;
    color: var(--muted);
    letter-spacing: 3px;
    text-transform: uppercase;
  }
  .card--front .brand-name { font-size: 30px; }

  .identity {
    width: 320px;
    display: flex;
    align-items: center;
    justify-content: flex-end;
    gap: 12px;
    padding-right: 34px;
  }
  .identity .brand-mark { width: 12px; height: 12px; }
  .identity .brand-name { font-size: 22px; line-height: 1.15; color: var(--ink); letter-spacing: 2px; }

  .divider { width: 2px; height: 170px; background: var(--accent); }

  .contact { padding-left: 34px; }
  .person-name {
    font-family: "Cinzel", Georgia, serif;
    font-weight: 500;
    font-size: 22px;
    color: var(--accent);
    letter-spacing: 1px;
    text-transform: uppercase;
  }
  .person-role { font-size: 15px; margin-bottom: 12px; }
  .address { font-size: 15px; line-height: 1.35; margin-bottom: 10px; }
  .contact-line { display: flex; align-items: center; gap: 10px; font-size: 15px; line-height: 1.6; }
  .contact-line svg { width: 14px; height: 14px; flex: none; }
  .web-domain { color: var(--accent); }
</style>
</head>
<body>

  <section class="card card--front" aria-label="Card front">
    <span class="brand-mark"></span>
    <span class="brand-name">Northline</span>
  </section>

  <section class="card card--back" aria-label="Card back">
    <div class="identity">
      <span class="brand-mark"></span>
      <span class="brand-name">Northline<br>Chiropractic</span>
    </div>
    <div class="divider"></div>
    <div class="contact">
      <p class="person-name">Marcus Hale</p>
      <p class="person-role">Director</p>
      <p class="address">1187 Cedar Ridge Lane<br>Salem, OR 97301</p>
      <p class="contact-line">
        <svg viewBox="0 0 24 24" fill="none" stroke="#4a86d4" stroke-width="2"><path d="M5 3h4l2 5-3 2a12 12 0 0 0 6 6l2-3 5 2v4a2 2 0 0 1-2 2A17 17 0 0 1 3 5a2 2 0 0 1 2-2z"/></svg>
        (555) 318-2046
      </p>
      <p class="contact-line">
        <svg viewBox="0 0 24 24" fill="none" stroke="#4a86d4" stroke-width="2"><rect x="3" y="5" width="18" height="14" rx="1"/><path d="M3 6l9 7 9-7"/></svg>
        hello@northlinechiro.com
      </p>
      <p class="contact-line">
        <svg viewBox="0 0 24 24" fill="none" stroke="#4a86d4" stroke-width="2"><circle cx="12" cy="12" r="9"/><path d="M3 12h18M12 3c3 3 3 15 0 18M12 3c-3 3-3 15 0 18"/></svg>
        <span>www.<span class="web-domain">northlinechiro</span>.com</span>
      </p>
    </div>
  </section>

</body>
</html>
```